WordPress Design for both website and landing page for an expert

I need a clean and stylish design for my new website. I work as an expert (see attached file WHY HOW WHAT), my product is expert opinion (reports) for company evaluations You can use all of the attached pictures colored or black / white. The person is me, you can add other pictures, if you want. The design should be clean and stylish, so you could use white, black, gray, silver and / or one additional color. I have added an idea about my website, see attached file CONCEPT WEBSITE If you have any more information, please do not hesitate to contact us 'Hesitate to ask me ...

```html
<!DOCTYPE html>
<html lang="en">
<head>
<meta charset="utf-8">
<title>Why / How I Do — Marten Holst</title>
<link href="https://fonts.googleapis.com/css2?family=Montserrat:wght@400;500;600;700&family=Noto+Serif:wght@400&display=swap" rel="stylesheet">
<style>
  :root {
    --bg: #000000;
    --text: #ffffff;
    --muted: #b9bcc2;
    --circle: #1f1f1f;
    --footer: #1b1b1b;
    --footer-text: #9a9ca1;
    --photo-light: #e9edf1;
    --photo-mid: #a9b6c4;
    --photo-dark: #3f6f9a;
  }
  * { box-sizing: border-box; margin: 0; padding: 0; }
  html, body { width: 1000px; height: 1200px; overflow: hidden; background: var(--bg); }
  body { position: relative; font-family: "Noto Serif", Georgia, serif; color: var(--text); }

  .brand {
    position: absolute; left: 30px; top: 44px;
    font-family: "Montserrat", Arial, sans-serif; font-weight: 600;
    font-size: 20px; letter-spacing: 1px; color: var(--text);
  }
  .page-title {
    position: absolute; left: 0; right: 0; top: 49px; text-align: center;
    font-family: "Montserrat", Arial, sans-serif; font-weight: 600;
    font-size: 12.5px; letter-spacing: 1.5px;
  }
  .close-btn { position: absolute; left: 933px; top: 47px; width: 18px; height: 18px; }

  .hero-photo {
    position: absolute; left: 115px; top: 164px; width: 385px; height: 314px;
    background: linear-gradient(160deg, var(--photo-light) 0%, var(--photo-mid) 55%, var(--photo-dark) 100%);
  }
  .hero-title {
    position: absolute; left: 0; right: 0; top: 258px; text-align: center;
    font-family: "Montserrat", Arial, sans-serif; font-weight: 400;
    font-size: 53px; line-height: 64px; letter-spacing: 7px; text-transform: uppercase;
  }

  .content { position: absolute; left: 235px; width: 560px; }
  .intro { top: 531px; font-size: 12.5px; line-height: 21.5px; color: var(--muted); }
  .section-title {
    top: 638px; font-family: "Montserrat", Arial, sans-serif; font-weight: 700; font-size: 21px;
  }
  .section-lead { top: 679px; width: 420px; font-size: 12.5px; line-height: 21.5px; color: var(--muted); }

  .feature { position: absolute; top: 771px; width: 250px; }
  .feature-one { left: 235px; }
  .feature-two { left: 528px; }
  .feature-icon { width: 108px; height: 108px; border-radius: 50%; background: var(--circle); }
  .feature-text { margin-top: 19px; font-size: 12.5px; line-height: 21.5px; color: var(--muted); }

  .cta {
    position: absolute; left: 235px; top: 1051px; width: 179px; height: 35px;
    border: 2px solid var(--text); border-radius: 18px;
    font-family: "Montserrat", Arial, sans-serif; font-weight: 700; font-size: 11px;
    letter-spacing: 0.5px; color: var(--text); text-transform: uppercase;
    display: flex; align-items: center; justify-content: center; text-decoration: none;
  }

  .site-footer {
    position: absolute; left: 0; bottom: 0; width: 1000px; height: 59px; background: var(--footer);
  }
  .copyright {
    position: absolute; left: 114px; top: 23px;
    font-family: "Montserrat", Arial, sans-serif; font-size: 11px; letter-spacing: 0.6px; color: var(--footer-text);
  }
  .social { position: absolute; top: 12px; display: flex; gap: 10px; left: 764px; }
  .social span { width: 34px; height: 34px; border-radius: 50%; background: #2a2a2a; display: block; }
</style>
</head>
<body>
  <header>
    <div class="brand">Holst</div>
    <div class="page-title">WHY / HOW I DO</div>
    <svg class="close-btn" viewBox="0 0 18 18" aria-label="Close menu">
      <path d="M1 1 L17 17 M17 1 L1 17" stroke="#ffffff" stroke-width="2" fill="none"/>
    </svg>
  </header>

  <main>
    <div class="hero-photo" role="img" aria-label="Photo of two business people reviewing a printed bar chart report"></div>
    <h1 class="hero-title">Economy is my<br>passion</h1>

    <p class="content intro">Economy is made in numbers. Sometimes it is difficult to find the right numbers.<br>I am always interested in finding out, how economy works and which numbers will tell<br>the really true story. I want to know it ...</p>

    <h2 class="content section-title">How I do?</h2>
    <p class="content section-lead">Each report begins with understanding. So I ask you questions and<br>listen very carefully.</p>

    <div class="feature feature-one">
      <div class="feature-icon" role="img" aria-label="Icon of a report with chart and magnifying glass"></div>
      <p class="feature-text">In the preparation of each report I<br>follow one defined&nbsp; process, but which<br>is tailored to the particular each<br>company is customized.</p>
    </div>
    <div class="feature feature-two">
      <div class="feature-icon" role="img" aria-label="Icon of a calculator and invoice with a dollar sign"></div>
      <p class="feature-text">This approach, coupled with<br>specialization in the area business<br>valuation, allows orders very fast<br>&amp; at the same time&nbsp; correct and<br>impeccable handle</p>
    </div>

    <a class="cta" href="#contact">Contact now!</a>
  </main>

  <footer class="site-footer">
    <p class="copyright">Copyright © 2018 Marten Holst. All Rights Reserved</p>
    <div class="social"><span></span><span></span><span></span></div>
  </footer>
</body>
</html>
```